Oriel Photography Business Card

I need a business card designed for a photography business based in Perth, Western Australia called Oriel Photography.

We specialise in wedding, event photography and portrait photography.

The business card must borrow the style of the attached logo.

The hex codes for the colours in the logo are:
#ED1D85 - Pink
#89C23E - Green
#37282F - Black

The name on the card will be:
Name: Tobrian
Phone: 0417395268
Website: www.orielphotography.example.com.au
social: orielphotography

I am open and happy to accept creative concepts.

I’d like some space at the back for writing notes and appointment details.

```html
<!DOCTYPE html>
<html lang="en">
<head>
<meta charset="UTF-8">
<title>Oriel Photography – Business Card</title>
<link href="https://fonts.googleapis.com/css2?family=Arimo:ital,wght@0,400;0,700;1,700&display=swap" rel="stylesheet">
<style>
  :root {
    --pink: #ED1D85;
    --green: #89C23E;
    --black: #37282F;
    --paper: #FFFFFF;
    --backdrop: #E6E6E6;
    --faint-pink: #FBE0E9;
  }
  html, body {
    margin: 0;
    padding: 0;
    width: 1200px;
    height: 1000px;
    overflow: hidden;
    background: var(--backdrop);
    font-family: "Arimo", Arial, sans-serif;
  }
  .canvas {
    position: relative;
    width: 1200px;
    height: 1000px;
  }
  .card {
    position: absolute;
    left: 220px;
    width: 760px;
    height: 434px;
    background: var(--paper);
    box-shadow: 0 2px 10px rgba(0,0,0,0.12);
  }
  .card--front { top: 45px; }
  .card--back  { top: 521px; }

  /* Front */
  .brand {
    position: absolute;
    left: 0;
    right: 0;
    top: 110px;
    text-align: center;
  }
  .brand__dot {
    display: block;
    width: 70px;
    height: 70px;
    margin: 0 auto 22px;
    border-radius: 50%;
    background: var(--pink);
  }
  .brand__name {
    margin: 0;
    color: var(--black);
    font-size: 20px;
    font-weight: 400;
    letter-spacing: 9px;
    text-transform: uppercase;
  }
  .brand__tagline {
    margin: 8px 0 0;
    color: var(--black);
    font-size: 14px;
    letter-spacing: 1.5px;
  }

  /* Back */
  .backdrop-circle {
    position: absolute;
    left: 120px;
    top: 115px;
    width: 230px;
    height: 230px;
    border-radius: 50%;
    background: var(--faint-pink);
  }
  .holder-name {
    position: absolute;
    left: 240px;
    top: 80px;
    margin: 0;
    color: var(--pink);
    font-size: 24px;
    font-weight: 700;
    font-style: italic;
  }
  .contact {
    position: absolute;
    left: 372px;
    top: 270px;
    margin: 0;
    padding: 2px 0 2px 12px;
    list-style: none;
    border-left: 2px solid var(--black);
  }
  .contact__item {
    display: flex;
    align-items: center;
    gap: 6px;
    height: 26px;
    color: var(--green);
    font-size: 19px;
    line-height: 1;
  }
  .contact__badge {
    display: inline-flex;
    align-items: center;
    justify-content: center;
    flex: 0 0 20px;
    width: 20px;
    height: 20px;
    background: var(--pink);
    color: var(--paper);
    font-size: 13px;
    font-weight: 700;
  }
</style>
</head>
<body>
<main class="canvas">
  <section class="card card--front" aria-label="Business card front">
    <div class="brand">
      <span class="brand__dot"></span>
      <h1 class="brand__name">Oriel Photography</h1>
      <p class="brand__tagline">Wedding-Event Photography-Portrait Photography</p>
    </div>
  </section>

  <section class="card card--back" aria-label="Business card back">
    <div class="backdrop-circle" role="img" aria-label="Faint brand emblem area"></div>
    <h2 class="holder-name">Tobrian</h2>
    <ul class="contact">
      <li class="contact__item"><span class="contact__badge">P</span>0417395268</li>
      <li class="contact__item"><span class="contact__badge">W</span>www.orielphotography.example.com.au</li>
      <li class="contact__item"><span class="contact__badge" aria-hidden="true"></span>social/orielphotography</li>
    </ul>
  </section>
</main>
</body>
</html>
```